Help Give House Painter “Fresh” Website Makeover!

A residential and commercial painting company based in Albuquerque, NM, USA needs a fresh, new, fun, and playful--yet, simple, elegant and professional--website made.

Here is a link to their existing site:

http://corvelcoatings.example/

We want to keep a similar site structure., So the navigation layout will stay the same. However, the video is too small, is too far over in the sidebar, and the overall design is amateur at best. We want something bright, colorful and bold!

We will need a space for the Video above the fold, and there needs to be space in the design for Testimonials, Specials and Images. It’s also very important to have the Pellham Roster awards that you see on his current website.

Please also include somewhere in the Design icons for YouTube, Facebook, Google+ and LinkedIn.

Here are some examples to look at to get your creative juices flowing!

http://brightloombrush.example/

http://www.tkvr.example/

http://www.marblow-tennick.example/

http://www.quarrypages.example/painting-company-niche-website/

http://www.brisklayoutdepot.example/website-templates/painting-company-website-template-53817.html

We have accounts at both lumavault.example and pixaroo.example. If you use placeholder images from there, that's fine. We can buy the images when and if your design is selected.

Target Market(s)

The audience is the average middle class homeowner to higher upper class. This should appeal to families, couples, and singles who own a home.

Industry/Entity Type

Residential

Font styles to use
Sans Serif

Requirements
Must have
• - - Lots of color! It's a site about painting homes. People like a variety of colors. Bring out your inner artist, and get bold with your colors!

- - A video place holder. As you can see, there is a video on the existing site, but it's small and hidden. Make it big and put it top left, or in the center.

- -Detailed and organized PSD structure. We're going to turn your design into a website, and to make that work soothly, we ask that you organize you PSD well: name your layers, keep things separated, group and ungroup as necessary, etc.

- A sidebar that goes down the right side of an interior page. We need a homepage, and also one [1] interior page template. We don't need you to make a design for each page. Just the homepage, followed by a simple interior page design that requires only the header/navigation, and a sidebar down the right side.
Should not have
• - Coding. This is a design project only.

```html
<!DOCTYPE html>
<html lang="en">
<head>
<meta charset="utf-8">
<title>Corvel Coatings – Residential &amp; Commercial Painting</title>
<link href="https://fonts.googleapis.com/css2?family=Lato:ital,wght@0,400;0,700;0,900;1,400;1,700&family=Open+Sans:wght@400;600;700&family=Oswald:wght@500&display=swap" rel="stylesheet">
<style>
:root{
  --blue:#1565c0;--blue-dark:#0b4f9c;--nav-top:#1a86d6;--nav-bot:#0a5fae;
  --red:#e0262b;--red-dark:#b3141a;--pink:#f9d6d8;
  --sky:#dbeaf7;--sky-2:#b9d6ef;--navy:#1d2a45;--navy-2:#24324f;
  --orange:#ff7a00;--cyan:#2fa8e4;--green:#6cb21c;
  --text:#333;--muted:#666;--gold:#d8a52a;--line:#cfd6de;
}
*{box-sizing:border-box;margin:0;padding:0}
html,body{width:756px;height:1200px;overflow:hidden}
body{position:relative;font-family:"Open Sans",Arial,sans-serif;color:var(--text);background:#fff}
.abs{position:absolute}

/* header */
.site-header{left:0;top:0;width:756px;height:76px;background:linear-gradient(90deg,var(--pink) 0,#fbe6e7 48%,#fff 58%)}
.brand{left:84px;top:21px;display:flex;align-items:center;gap:8px}
.brand-dot{width:34px;height:34px;border-radius:50%;background:var(--blue)}
.brand-name{font-family:"Lato",sans-serif;font-weight:900;font-size:21px;color:var(--blue);letter-spacing:.3px}
.award{top:8px;width:34px;height:48px;border-radius:6px 6px 17px 17px;background:linear-gradient(#f1cf5a,var(--gold))}
.award-label{top:61px;font-size:7px;font-weight:600;color:var(--blue);width:70px;text-align:center}
.phone{left:563px;top:12px;display:flex;align-items:center;gap:6px;font-family:"Lato",sans-serif;font-size:16px;color:var(--red)}
.estimate-btn{left:540px;top:43px;width:134px;height:21px;border-radius:3px;background:linear-gradient(var(--nav-top),var(--nav-bot));color:#fff;font-family:"Lato",sans-serif;font-weight:700;font-size:11px;text-align:center;line-height:21px}

/* nav */
.main-nav{left:0;top:76px;width:756px;height:29px;background:linear-gradient(var(--nav-top),var(--nav-bot));box-shadow:0 2px 3px rgba(0,0,0,.25)}
.main-nav ul{list-style:none;display:flex;gap:14px;position:absolute;left:82px;top:9px}
.main-nav li{font-family:"Lato",sans-serif;font-weight:700;font-size:9px;color:#fff;text-transform:uppercase}
.main-nav li.active{border-bottom:1px solid #fff;padding-bottom:3px}

/* hero */
.hero-art{left:0;top:105px;width:405px;height:300px;background:linear-gradient(160deg,#f23a35,var(--red) 50%,var(--red-dark))}
.video{left:82px;top:130px;width:248px;height:146px;background:#fff;padding:5px;border-radius:3px;box-shadow:0 2px 6px rgba(0,0,0,.4)}
.video-frame{width:100%;height:116px;background:linear-gradient(135deg,#b9c7a8,#d4d8ca 50%,#8d8e99)}
.video-controls{height:20px;background:#1c1c1c;display:flex;align-items:center;gap:8px;padding:0 6px}
.progress{flex:1;height:4px;background:#444;border-radius:2px}
.progress span{display:block;width:40%;height:100%;background:#2a7fd1;border-radius:2px}
.hero-title{left:60px;top:300px;width:290px;text-align:center;font-family:"Oswald",sans-serif;font-weight:500;font-size:23px;line-height:32px;color:#fff;text-shadow:0 2px 3px rgba(0,0,0,.5)}

.estimate-form{left:474px;top:126px;width:194px}
.estimate-form h2{font-family:"Lato",sans-serif;font-weight:700;font-size:14px;color:var(--blue-dark);text-align:center;margin-bottom:11px}
.estimate-form p{font-size:7px;line-height:9px;color:#444;margin-bottom:6px}
.field{height:21px;border:1px solid var(--line);margin-bottom:3px;font-size:8px;color:#777;padding:5px 6px}
.field.area{height:43px}
.captcha{width:83px;height:21px;border:1px solid var(--line);font-size:9px;color:#555;padding:4px 15px;margin-bottom:3px;letter-spacing:2px}
.submit{height:21px;margin-top:4px;background:linear-gradient(var(--nav-top),var(--nav-bot));color:#fff;font-family:"Lato",sans-serif;font-weight:700;font-size:11px;text-align:center;line-height:21px}

/* welcome */
.welcome-band{left:0;top:405px;width:756px;height:180px;background:linear-gradient(var(--sky),#eef5fb 50%,var(--sky-2))}
.welcome-box{left:83px;top:430px;width:590px;height:125px;background:#fff;border:1px solid #d8e2ec;border-radius:3px;padding:9px 12px}
.welcome-box h1{font-family:"Lato",sans-serif;font-weight:700;font-size:13px;color:var(--blue-dark);margin-bottom:3px}
.welcome-box h1 em{font-style:normal;color:var(--red)}
.welcome-box p{font-size:9px;line-height:15px;color:#444}

/* feature cards */
.feature-band{left:0;top:585px;width:756px;height:347px;background:radial-gradient(ellipse at 50% 40%,var(--navy-2),var(--navy) 75%)}
.card{top:622px;width:175px;height:258px;color:#fff;text-align:center;padding-top:14px}
.card h3{font-family:"Lato",sans-serif;font-weight:700;font-size:13px;line-height:17px}
.card .photo{margin:9px auto 0;width:154px;height:97px;border:5px solid #fff}
.card p{font-size:8px;line-height:13px;color:#1a1a1a;padding:8px 14px 0;height:54px;overflow:hidden}
.card .more{font-size:8px;font-weight:700;color:#1a1a1a;margin-top:6px}
.card.orange{left:85px;background:linear-gradient(var(--orange),#ff9a1a)}
.card.blue{left:292px;background:linear-gradient(#2b9ad9,#4fc0f0)}
.card.green{left:495px;background:linear-gradient(#3f9a10,#86c41f)}

/* review */
.review-band{left:0;top:932px;width:756px;height:206px;background:linear-gradient(#eef5fb,var(--sky) 60%,#b6d2ec)}
.review-title{left:0;top:953px;width:756px;text-align:center;font-family:"Lato",sans-serif;font-weight:700;font-size:18px;color:var(--blue-dark)}
.review-title em{font-style:normal;color:var(--red)}
.review-sub{left:0;top:977px;width:756px;text-align:center;font-family:"Lato",sans-serif;font-size:9px;color:#666}
.divider{left:225px;top:999px;width:306px;height:1px;background:#c6d3e0}
.stars{left:360px;top:992px;font-size:10px;color:#f2b400;letter-spacing:1px;background:var(--sky);padding:0 3px}
.quote{left:83px;top:1018px;width:490px;height:60px;background:#f2f2f2;border-radius:3px;padding:6px 12px;font-family:"Lato",sans-serif;font-style:italic;font-size:8.3px;line-height:16px;color:#333}
.quote b{font-size:20px;color:#bbb;font-style:normal;vertical-align:-5px;margin-right:3px}
.avatar{left:587px;top:1013px;width:74px;height:74px;border-radius:50%;border:4px solid #fff;background:linear-gradient(#e9eef3,#b8c4d0);box-shadow:0 1px 4px rgba(0,0,0,.25)}
.reviewer{left:430px;top:1090px;width:160px;text-align:right;font-family:"Lato",sans-serif;font-style:italic;font-weight:700;font-size:8px;color:#333}

/* footer */
.site-footer{left:0;top:1138px;width:756px;height:62px;background:var(--navy);text-align:center;color:#fff}
.site-footer ul{list-style:none;display:flex;justify-content:center;margin-top:21px;font-family:"Lato",sans-serif;font-weight:700;font-size:7.5px}
.site-footer li+li::before{content:"|";margin:0 5px}
.site-footer small{display:block;margin-top:4px;font-size:7px;letter-spacing:.4px}
</style>
</head>
<body>

<header class="abs site-header">
  <div class="abs brand"><span class="brand-dot"></span><span class="brand-name">CORVEL COATINGS</span></div>
  <div class="abs award" style="left:409px"></div>
  <div class="abs award-label" style="left:391px">Exterior Painting</div>
  <div class="abs award" style="left:475px"></div>
  <div class="abs award-label" style="left:457px">Interior Painting</div>
  <div class="abs phone">
    <svg width="15" height="15" viewBox="0 0 16 16"><circle cx="8" cy="8" r="7" fill="none" stroke="#1565c0" stroke-width="1.4"/><path d="M5.5 4.5l1.4 1.6-.8 1.1c.5 1 1.3 1.8 2.3 2.3l1.1-.8 1.6 1.4-.9 1.2c-2.8-.4-5.1-2.7-5.5-5.5z" fill="#1565c0"/></svg>
    123 456 7890
  </div>
  <div class="abs estimate-btn">FREE ESTIMATES</div>
</header>

<nav class="abs main-nav">
  <ul>
    <li class="active">Home</li><li>About Us</li><li>Residential Painting</li><li>Commercial Painting</li><li>FAQ</li><li>Specials</li><li>Blog</li><li>Testimonials</li><li>Contact Us</li>
  </ul>
</nav>

<section>
  <div class="abs hero-art" role="img" aria-label="Red paint roller stroke across the hero area"></div>
  <div class="abs video">
    <div class="video-frame" role="img" aria-label="Video still of a painter working on a wall"></div>
    <div class="video-controls">
      <svg width="8" height="9" viewBox="0 0 8 9"><path d="M0 0l8 4.5L0 9z" fill="#fff"/></svg>
      <svg width="10" height="9" viewBox="0 0 10 9"><path d="M0 3h2l3-3v9L2 6H0z" fill="#fff"/></svg>
      <div class="progress"><span></span></div>
      <svg width="9" height="9" viewBox="0 0 9 9"><path d="M0 3V0h3M6 0h3v3M9 6v3H6M3 9H0V6" fill="none" stroke="#fff" stroke-width="1.3"/></svg>
    </div>
  </div>
  <h2 class="abs hero-title">Residential &amp; Commercial<br>Painting Company</h2>

  <form class="abs estimate-form">
    <h2>Schedule Free Estimate</h2>
    <p>How to Schedule an Estimae Requesting an estimate online is very simple and easy. Fill out the Form below and we will send you a rough quote to your email. We may also call you if we have any more questions.</p>
    <div class="field">First Name</div>
    <div class="field">Email</div>
    <div class="field">Phone</div>
    <div class="field area">Decribe what needs to be done.</div>
    <div class="captcha">A<sub>6</sub>0 C</div>
    <div class="field">Please type the following</div>
    <div class="submit">SUBMIT</div>
  </form>
</section>

<section>
  <div class="abs welcome-band"></div>
  <article class="abs welcome-box">
    <h1>Welcome To CORVEL <em>COATINGS</em></h1>
    <p>Corvel Coatings does jobs as small as a bathroom up to large commercial projects right here in Albuquerque and Rio Rancho. Extensive as an entire apartment exterior, to a kitchen and all home interior, no job is too big or too small for Corvel Coatings of Albuquerque. Corvel Coatings is staffed with the best painters for the highest quality paint jobs. Corvel Coatings is not a community's average house painter staffing company, but this painting company is staffed with professional painters that pride themselves on successfully completing every job.</p>
  </article>
</section>

<section>
  <div class="abs feature-band"></div>
  <article class="abs card orange">
    <h3>Our Painting<br>In Albuquerque</h3>
    <div class="photo" role="img" aria-label="Couple painting a wall green" style="background:linear-gradient(135deg,#f4efe6,#cfe7a6)"></div>
    <p>Corvel Coatings does jobs as small as a bathroom up to large commercial projects right here in Albuquerque.</p>
    <div class="more">Read More ››</div>
  </article>
  <article class="abs card blue">
    <h3>Albuquerque<br>Painter Videos</h3>
    <div class="photo" role="img" aria-label="Paint roller on an orange wall" style="background:linear-gradient(135deg,#e9a53a,#c9791a)"></div>
    <p>TWe have shot a ton of videos with Dale answering all of your most frequently asked questions. We want</p>
    <div class="more">Read More ››</div>
  </article>
  <article class="abs card green">
    <h3>Happy Albuquerque<br>Painting Customers</h3>
    <div class="photo" role="img" aria-label="Woman rolling light blue paint on a wall" style="background:linear-gradient(135deg,#eef3f7,#9cc7e6)"></div>
    <p>100% Customer Satisfaction is our Ultimate Goal. We are proud to have served so many clients in an around</p>
    <div class="more">Read More ››</div>
  </article>
</section>

<section>
  <div class="abs review-band"></div>
  <h2 class="abs review-title">Our Customer <em>Review</em></h2>
  <p class="abs review-sub">Lorem ipsum dolor sit amet, consectetur Donec a consequat mag &nbsp;Aenean eu velit &nbsp;Aenean sollicitudin</p>
  <div class="abs divider"></div>
  <div class="abs stars">★★★</div>
  <blockquote class="abs quote"><b>“</b>Lorem sum dolor sit amet, consectetuer adipiscing elit, sed diam nonummy nibh euismod tincidunt ut laoreet re agn aliqam erat volutpat wisi enim ad minim veniam, quis nostrud exerci tation ullamcorper suscipit lobortis nisl ut aliquip modo conseuatis autem vel eum iriure dolor in hendrerit in vulputate velit esse molestie consequat, vel illum dolore eu.</blockquote>
  <div class="abs avatar" role="img" aria-label="Portrait of the reviewing customer"></div>
  <div class="abs reviewer">Tamsin, Brightfield Co , USA</div>
</section>

<footer class="abs site-footer">
  <ul><li>HOME</li><li>ABOUT US</li><li>RESIDENTIAL PAINTING</li><li>COMMERCIAL PAINTING</li><li>FAQ</li><li>SPECIALS</li><li>BLOG</li><li>TESTIMONIALS</li><li>CONTACT US</li></ul>
  <small>© 2015 CORVEL COATINGS. ALL RIGHT RESERVED.</small>
</footer>

</body>
</html>
```